Fancy flyer to entice High School Students

http://kestrelvane.com needs a marketing slick/flyer to pass out. The marketing text is below(feel free to place where you think appropriate).

* 8th grade to 12th grade (or 8th graders to 12th graders)
* Land a real job internship(instead of Pelkroft)
* 100's of internships available
* Learn how to start your own business out of High School making way more than minimum wage
* In college when interviewing for an internship don't be the guy that answers "no, sorry, this would be my first internship" putting you at a huge disadvantage"
* Fill in the Contact Us form at http://kestrelvane.com at the bottom left corner to find out more information

We will be evaluating design with this blog post in mind....
http://trundlepostnotes.com/color-influence-buyers/

We like attention grabbing contact us type stuff and calls to action. If you feel it is appropriate to change the marketing text to make your flyer stand out, please feel free. I am not the best at marketing and am the first to admit it.
Updates

A simple 8.5 x 11 flyer would be great.

Target Market(s)

High School students, male and female with high grade point averages(smart students). For the top 20% of their class.

Industry/Entity Type

Marketing

Requirements
Must have
• good call to action

```html
<!DOCTYPE html>
<html lang="en">
<head>
<meta charset="utf-8">
<title>Kestrelvane Internship Flyer</title>
<link rel="stylesheet" href="https://fonts.googleapis.com/css2?family=PT+Sans+Narrow:wght@700&family=Open+Sans:wght@400;600&family=Arimo:wght@400;700&display=swap">
<style>
  :root{
    --ink-dark:#3a3a3a;
    --footer:#3b3b3b;
    --navy:#2e3a8c;
    --pink:#d91b63;
    --pink-soft:#e0459a;
    --amber:#c97d1f;
    --green:#3fb54a;
    --violet:#6a3f9c;
    --label-orange:#f3a02f;
    --cream-top:#fdf5e4;
    --cream-bottom:#f2c57f;
    --band-orange:#eba23f;
  }
  html,body{margin:0;padding:0;overflow:hidden;background:#ffffff;}
  .flyer{position:relative;width:931px;height:1200px;overflow:hidden;background:var(--cream-top);}
  .hero-photo{position:absolute;left:0;top:0;width:931px;height:600px;
    background:linear-gradient(180deg,#3d6a52 0%,#6d8a72 35%,#c9c4b8 62%,#efece6 80%,#a9865e 100%);}
  .waves{position:absolute;left:0;top:0;width:931px;height:1200px;}
  .headline{position:absolute;left:304px;top:552px;margin:0;
    font-family:"PT Sans Narrow",sans-serif;font-weight:700;font-size:56px;line-height:54px;
    color:var(--ink-dark);letter-spacing:0.5px;white-space:nowrap;}
  .cta{position:absolute;left:304px;top:700px;margin:0;font-family:"PT Sans Narrow",sans-serif;font-weight:700;white-space:nowrap;line-height:56px;}
  .cta-label{color:var(--navy);font-size:40px;}
  .cta-phone{color:var(--ink-dark);font-size:47px;margin-left:14px;}
  .students-photo{position:absolute;left:0;top:650px;width:290px;height:330px;
    background:linear-gradient(180deg,#b07a5a 0%,#7d6a55 40%,#5b7894 70%,#8c8c8c 100%);border-radius:60px 60px 8px 8px;}
  .shell-art{position:absolute;left:48px;top:940px;width:218px;height:120px;
    background:radial-gradient(ellipse at 50% 60%,#fff1d6 0%,#f7d7a0 55%,#eab46a 100%);border-radius:50% 50% 40% 40%;}
  .placement-note{position:absolute;left:20px;top:1064px;width:210px;margin:0;text-align:center;
    font-family:"Arimo",sans-serif;font-size:12px;line-height:15px;color:#3a3a3a;}
  .points{position:absolute;left:290px;top:794px;width:641px;margin:0;padding:0;list-style:none;}
  .point{box-sizing:border-box;margin:0 0 10px;padding:5px 48px 5px 14px;border-radius:10px 0 0 10px;
    font-family:"Open Sans",sans-serif;font-weight:600;font-size:18px;line-height:25px;color:#ffffff;}
  .point--pink{background:var(--pink);}
  .point--amber{background:var(--amber);}
  .point--green{background:var(--green);}
  .point--rose{background:var(--pink-soft);}
  .point--violet{background:var(--violet);}
  .bottom-band{position:absolute;left:262px;top:1086px;width:669px;height:26px;background:var(--band-orange);}
  .contact-footer{position:absolute;left:0;top:1120px;width:931px;height:80px;background:var(--footer);
    font-family:"Arimo",sans-serif;font-size:21px;color:#ffffff;}
  .contact-item{position:absolute;top:16px;margin:0;line-height:26px;}
  .contact-item dt{color:var(--label-orange);font-weight:700;}
  .contact-item dd{margin:0;}
  .contact-item--email{left:54px;}
  .contact-item--web{left:307px;}
  .contact-item--address{left:589px;}
  .contact-item--address dt span{color:#ffffff;font-weight:400;}
</style>
</head>
<body>
<main class="flyer">
  <div class="hero-photo" role="img" aria-label="Photo of high school students in uniforms sitting at desks in a classroom"></div>

  <svg class="waves" viewBox="0 0 931 1200" aria-hidden="true">
    <defs>
      <linearGradient id="creamFade" x1="0" y1="0" x2="0" y2="1">
        <stop offset="0" stop-color="var(--cream-top)"/>
        <stop offset="0.55" stop-color="#fbe6c2"/>
        <stop offset="1" stop-color="var(--cream-bottom)"/>
      </linearGradient>
    </defs>
    <path d="M0,590 C250,500 620,520 931,560 L931,1120 L0,1120 Z" fill="url(#creamFade)"/>
    <path d="M0,484 C160,468 330,466 480,478 C300,480 150,500 0,532 Z" fill="var(--pink)"/>
    <path d="M0,528 C200,470 600,462 931,544 L931,566 C600,500 250,500 0,598 Z" fill="var(--footer)"/>
    <path d="M62,462 C300,442 650,452 931,540 L931,552 C650,464 300,452 62,462 Z" fill="var(--green)"/>
  </svg>

  <h1 class="headline">WE PROVIDE<br>REAL INTERSHIP !</h1>
  <p class="cta"><span class="cta-label">Contact us today</span><span class="cta-phone">(720) 555-0148</span></p>

  <div class="students-photo" role="img" aria-label="Photo of a group of smiling teenage students holding books"></div>
  <div class="shell-art" role="img" aria-label="Illustration of an open seashell holding a pearl"></div>
  <p class="placement-note">feel free to place where<br>you think appropriate</p>

  <ul class="points">
    <li class="point point--pink">8th graders to 12th graders)</li>
    <li class="point point--amber">Land a real job internship (instead of Pelkroft)</li>
    <li class="point point--green">100's of internships available</li>
    <li class="point point--rose">Learn how to start your own business out of High School making way more than minimum wage</li>
    <li class="point point--violet">In college when interviewing for an internship don't be the guy that answers "no, sorry, this would be my first internship" putting you at a huge disadvantage"</li>
  </ul>

  <div class="bottom-band"></div>

  <footer class="contact-footer">
    <dl class="contact-item contact-item--email"><dt>Email</dt><dd>info@kestrelvane.com</dd></dl>
    <dl class="contact-item contact-item--web"><dt>Web</dt><dd>www.kestrelvane.com</dd></dl>
    <dl class="contact-item contact-item--address"><dt>Add <span>: 4180 W. 96th Ave.</span></dt><dd>#207, Halden, CO 80031</dd></dl>
  </footer>
</main>
</body>
</html>
```